Truck Outfitters and Trailer Hitch Retailer Website

We are working with a hitch installer in California called Brisk Tow. They sell and install trailer hitches, bedliners for trucks, and pickup truck accessories.
Some sites to use for content/competitors:
https://www.varlomi.com/pick-up-outfitters
https://bramwells-rigs.com
https://www.thetowlodge.com
https://towlodgeinccom.quenrivsites.com
Some sites to use for inspiration:
https://www.ironmarkcouplers.com
https://quietcouplers.com
https://velmatow.com/
https://www.harborcoat.com
https://www.rugged-trailpath.com
Thank you for taking the time to consider designing a website for us. We are web developers based in Stockton, CA, USA. Most of our projects go through the same process. Understanding this process may help you win a project with us. We custom-code all of our websites in-house. We don’t have any requirements as to what tools you use for your design, but we prefer Figma files. For any design that we label as four-stars, we send it to the client for review. The client picks the final design they want us to use. Once we complete this process, we will continue to show additional clients all the four-star sites and purchase them later. Your designs will have multiple chances to sell. For better chances of success, we ask that you follow these guidelines.
IMAGES:
If you use any images or icons in the design, we ask that you have a link to the asset so we can purchase the image/icon. Most of the designs we submit do not have the customer’s images on them unless they have some great images. Be creative; show us the feeling you are trying to portray with your image choices. Use any royalty-free site you choose. We subscribe to Adobe and mainly use their images, but we can purchase images outside of Adobe.
PLEASE NOTE: we will not submit designs to clients with watermarks on the images.
FONTS:
We ask that you identify the fonts used in the design. This can be done in a message if you want. We typically use Google Fonts and Adobe Fonts.
CONTENT:
We're always open to different content and ideas. We often submit designs with stock images so the client can see our vision. We typically take pictures after the website launch to use their images with our vision. Lorem Ipsum is fine for paragraphs, but we ask that you write the headers in correct English. We want to be able to show the vision and identify the sections of the website.
INSPIRATION:
We typically add a couple of links in the brief of websites we like to help you get started in your design.
REVISIONS:
We do not often ask for revisions of the designs unless we see something in the design that may not appeal to the client. If there are slight changes that we want to make, we do that in the development process.
FEEDBACK:
We rarely give feedback on designs during the design process. We are working on many website projects and do not have the time to provide feedback. We usually respond if your request is well thought out and asks specific questions, but a note asking “feedback, please” usually goes unanswered
Number of Pages Required
1 page
Look and feel
Each slider illustrates characteristics of the customer's brand and the style your logo design should communicate.

```html
<!DOCTYPE html>
<html lang="en">
<head>
<meta charset="utf-8">
<title>Brisk Tow – Trailer Hitches &amp; Truck Outfitters</title>
<link rel="stylesheet" href="https://fonts.googleapis.com/css2?family=Orbitron:wght@700;800;900&family=Roboto:wght@400;500;700&display=swap">
<style>
:root{
  --red:#e3070e;
  --black:#0d0d0d;
  --ink:#111111;
  --panel:#1b1b1b;
  --card:#222222;
  --grey:#8a8a8a;
  --white:#ffffff;
  --field:#e6e6e6;
}
*{margin:0;padding:0;box-sizing:border-box}
html,body{width:1200px;height:3915px;overflow:hidden}
body{position:relative;background:var(--black);color:var(--white);font-family:'Roboto',sans-serif}
.abs{position:absolute}
.display{font-family:'Orbitron',sans-serif;font-weight:900;letter-spacing:2px;text-transform:uppercase}
.eyebrow{font-size:15px;color:var(--grey);text-transform:uppercase;font-weight:500}
.rule{position:absolute;height:3px;width:46px;background:var(--red)}

/* header */
.site-header{left:0;top:0;width:1200px;height:112px;background:var(--ink)}
.logo-tab{left:90px;top:0;width:206px;height:145px;background:var(--ink);clip-path:polygon(0 0,100% 0,100% 70%,85% 100%,15% 100%,0 70%)}
.brand{font-family:'Roboto',sans-serif;font-weight:700;font-size:24px;color:var(--white);text-transform:uppercase;letter-spacing:1px;display:flex;align-items:center;gap:8px}
.brand .mark{width:14px;height:14px;background:var(--red);display:inline-block}
.nav{left:403px;top:47px;display:flex;gap:27px;font-size:13px;font-weight:700;text-transform:uppercase}
.nav a{color:var(--white);text-decoration:none}
.nav a.active{color:var(--red);text-decoration:underline}
.socials{left:775px;top:0;display:flex;height:112px}
.socials span{width:38px;height:112px;border-left:1px solid #333;background:#1d1d1d;display:flex;align-items:center;justify-content:center}
.socials span.on{background:var(--red)}
.socials span i{width:10px;height:10px;border:2px solid var(--white);border-radius:2px}
.call{left:925px;top:0;width:275px;height:112px;background:var(--red);display:flex;align-items:center;gap:16px;padding-left:28px}
.call small{display:block;font-size:10px;font-weight:500}
.call strong{font-size:19px}

/* hero */
.hero-photo{left:0;top:112px;width:1200px;height:700px;background:linear-gradient(100deg,#7d8fa5 0%,#a7b2bd 30%,#6f7780 55%,#4a4f55 80%,#2e3135 100%)}
.hero-box{left:284px;top:286px;width:634px;height:208px;border:3px solid var(--red);background:rgba(90,90,90,.75);text-align:center;padding-top:28px}
.hero-box h1{font-size:48px}
.hero-box p{font-size:20px;line-height:31px;margin-top:14px}
.btn{display:inline-flex;align-items:center;justify-content:center;background:var(--red);color:var(--white);font-weight:700;font-size:15px;text-transform:uppercase}
.hero-btn{left:529px;top:468px;width:141px;height:46px}
.slider-dots{left:1138px;top:318px;display:flex;flex-direction:column;gap:11px}
.slider-dots i{width:12px;height:12px;border:1.5px solid var(--white);border-radius:50%}
.slider-dots i.on{background:var(--white)}

/* about */
.shot{background:linear-gradient(135deg,#5d6a6d,#2c3033)}
.frame{border:2px solid var(--red)}
.about-text{left:726px;top:896px;width:362px}
.about-text h2{font-size:38px;margin-top:2px}
.about-text p{font-size:14.5px;line-height:25.6px;text-align:justify;margin-top:28px}
.about-text p+p{margin-top:16px}

/* services */
.services-bg{left:0;top:1486px;width:1200px;height:580px;background:var(--panel)}
.center{left:0;width:1200px;text-align:center}
.svc-card{top:1653px;width:475px;height:307px}
.hex{width:80px;height:90px;background:var(--white);clip-path:polygon(50% 0,100% 25%,100% 75%,50% 100%,0 75%,0 25%)}
.svc-title{top:1997px;width:475px;text-align:center;font-size:18px;font-weight:700;text-transform:uppercase}
.arrow{top:1788px;width:36px;height:36px;border-radius:50%;background:#2c2c2c}

/* testimonials */
.quote{top:2461px;width:305px;height:258px;background:var(--card);padding:24px 23px}
.stars{color:#f5b800;font-size:15px;letter-spacing:2px}
.quote p{font-size:13.5px;line-height:23px;margin-top:12px}
.quote hr{border:0;border-top:1px solid #555;margin:16px 0 14px}
.person{display:flex;align-items:center;gap:20px}
.avatar{width:56px;height:56px;border-radius:50%;background:linear-gradient(135deg,#c59a78,#6d5445)}
.person b{font-size:16px;display:block}
.person small{font-size:12px}
.dots{top:2759px;left:560px;display:flex;gap:10px}
.dots i{width:11px;height:11px;border-radius:50%;background:#444}
.dots i.on{background:var(--red)}

/* contact */
.contact-photo{left:0;top:2871px;width:1200px;height:730px;background:radial-gradient(ellipse at 28% 40%,#4a4d50 0%,#2a2b2d 45%,#151515 100%)}
.label{font-size:14px}
.field{background:var(--field);border:1px solid #bbb}

/* footer */
.f-head{top:3638px;font-size:18px;font-weight:700;text-transform:uppercase}
.f-links{top:3681px;list-style:none;font-size:14px}
.f-links li{height:41px;padding-left:35px;position:relative}
.f-links li::before{content:"»";position:absolute;left:0;color:var(--red)}
.ic{width:38px;height:38px;background:var(--red);display:flex;align-items:center;justify-content:center}
.c-text{font-size:12px;line-height:19px}
.c-text b{font-size:14px;font-weight:700}
.foot-rule{left:111px;top:3854px;width:978px;border-top:1px solid #444}
.copy{left:464px;top:3874px;font-size:12px}
.f-social{left:940px;top:3866px;display:flex;gap:6px}
.f-social span{width:33px;height:33px;background:#eee;display:flex;align-items:center;justify-content:center}
.f-social span.on{background:var(--red)}
.f-social i{width:10px;height:10px;border:2px solid #222;border-radius:2px}
.f-social span.on i{border-color:#fff}
</style>
</head>
<body>

<!-- Hero photo -->
<div class="abs hero-photo" role="img" aria-label="Close-up of a trailer tongue jack and hitch on an asphalt road"></div>
<svg class="abs" style="left:0;top:540px" width="1200" height="300" viewBox="0 540 1200 300">
  <polygon points="0,588 418,790 1200,560 1200,840 0,840" fill="#0d0d0d"/>
  <polygon points="98,636 418,805 990,620 418,775" fill="#e3070e"/>
</svg>

<!-- Header -->
<header class="abs site-header"></header>
<div class="abs logo-tab"></div>
<div class="abs brand" style="left:118px;top:86px">Brisk Tow<span class="mark"></span></div>
<nav class="abs nav">
  <a class="active">Home</a><a>About Us</a><a>Services</a><a>Contact Us</a>
</nav>
<div class="abs socials"><span><i></i></span><span class="on"><i></i></span><span><i></i></span><span><i></i></span></div>
<div class="abs call">
  <svg width="44" height="44" viewBox="0 0 24 24"><path fill="#fff" d="M6.6 10.8a15.1 15.1 0 0 0 6.6 6.6l2.2-2.2c.3-.3.7-.4 1-.2 1.1.4 2.3.6 3.6.6.6 0 1 .4 1 1V20c0 .6-.4 1-1 1A17 17 0 0 1 3 4c0-.6.4-1 1-1h3.5c.6 0 1 .4 1 1 0 1.3.2 2.5.6 3.6.1.3 0 .7-.2 1z"/></svg>
  <div><small>REQUEST A CALL:</small><strong>+1 (888) 888 8888</strong></div>
</div>

<!-- Hero content -->
<div class="abs hero-box">
  <h1 class="display">Brisk Tow</h1>
  <p>Lorem ipsum dolor sit amet, consectetur adipiscing elit, sed<br>eiusmod incididunt laborea.</p>
</div>
<a class="abs btn hero-btn">Get Started</a>
<div class="abs slider-dots"><i></i><i class="on"></i><i></i><i></i></div>

<!-- About -->
<div class="abs frame" style="left:150px;top:909px;width:459px;height:428px"></div>
<div class="abs shot" style="left:111px;top:873px;width:463px;height:236px" role="img" aria-label="Truck rear bumper with spare tire and tail light"></div>
<div class="abs shot" style="left:111px;top:1109px;width:238px;height:193px;background:linear-gradient(135deg,#3a3a36,#6b5a3a)" role="img" aria-label="Off-road tire beside the bumper"></div>
<div class="abs shot" style="left:358px;top:1119px;width:278px;height:243px;background:linear-gradient(135deg,#5f7a4d,#8d8f8c 55%,#3b3d3f)" role="img" aria-label="Hand coupling a trailer to a ball hitch"></div>

<div class="abs about-text">
  <div class="eyebrow">Who We Are</div>
  <h2 class="display">About Us</h2>
  <p>Lorem ipsum dolor sit amet, consectetur adipiscing elit, sed do eiusmod tempor incididunt ut labore et dolore magna aliqua. Ut enim ad minim veniam, quis nostrud exercitation ullamco laboris nisi ut aliquip ex ea commodo consequat. Duis aute irure dolor in reprehenderit in voluptate velit esse cillum dolore eu fugiat nulla pariatur.</p>
  <p>Lorem ipsum dolor sit amet, consectetur adipiscing elit, sed do eiusmod tempor incididunt ut labore et dolore magna aliquea.</p>
</div>
<div class="rule" style="left:693px;top:964px"></div>
<a class="abs btn" style="left:726px;top:1297px;width:147px;height:50px">Learn More</a>

<!-- Services -->
<div class="abs services-bg"></div>
<svg class="abs" style="left:0;top:2040px" width="1200" height="300" viewBox="0 2040 1200 300">
  <polygon points="0,2046 782,2250 1200,2040 1200,2340 0,2340" fill="#0d0d0d"/>
  <polygon points="212,2100 782,2282 1100,2112 782,2238" fill="#e3070e"/>
</svg>
<div class="abs center eyebrow" style="top:1540px">What We Do</div>
<h2 class="abs center display" style="top:1556px;font-size:38px">Our Services</h2>
<div class="rule" style="left:578px;top:1603px"></div>

<div class="abs arrow" style="left:43px"><svg width="36" height="36"><path d="M22 9l-9 9 9 9" stroke="#e3070e" stroke-width="4" fill="none"/></svg></div>
<div class="abs arrow" style="left:1121px"><svg width="36" height="36"><path d="M14 9l9 9-9 9" stroke="#e3070e" stroke-width="4" fill="none"/></svg></div>

<div class="abs shot svc-card" style="left:111px;background:linear-gradient(120deg,#8a6a45,#9aa3ad 45%,#4b5560)" role="img" aria-label="Trailer hitch coupler mounted on a steel frame"></div>
<div class="abs shot svc-card" style="left:614px;background:linear-gradient(180deg,#9aa4a0 0%,#3f5a35 40%,#6c6c6a 75%,#555 100%)" role="img" aria-label="Semi truck pulling a flatbed trailer on a highway"></div>
<div class="abs hex" style="left:309px;top:1890px"></div>
<div class="abs hex" style="left:811px;top:1890px"></div>
<div class="abs svc-title" style="left:111px">Sell and Install Trailer Hitches</div>
<div class="abs svc-title" style="left:614px;text-decoration:underline">Bedliners for Trucks</div>

<!-- Testimonials -->
<div class="abs center eyebrow" style="top:2354px">Testimonials</div>
<h2 class="abs center display" style="top:2370px;font-size:38px">What Our Clients Say</h2>
<div class="rule" style="left:578px;top:2418px"></div>

<div class="abs quote" style="left:111px">
  <div class="stars">★★★★★</div>
  <p>Lorem ipsum dolor sit amet, consectetur adipiscing elit, sed do eiusmod tempor incididunt ut labore et dolore magna aliqu ad minim veniam, quisea.</p>
  <hr>
  <div class="person"><div class="avatar" role="img" aria-label="Client portrait"></div><div><b>JOHN SMITH,</b><small>USA</small></div></div>
</div>
<div class="abs quote" style="left:447px">
  <div class="stars">★★★★★</div>
  <p>Lorem ipsum dolor sit amet, consectetur adipiscing elit, sed do eiusmod tempor incididunt ut labore et dolore magna aliqu ad minim veniam, quisea.</p>
  <hr>
  <div class="person"><div class="avatar" role="img" aria-label="Client portrait"></div><div><b>LAURA,</b><small>USA</small></div></div>
</div>
<div class="abs quote" style="left:783px">
  <div class="stars">★★★★★</div>
  <p>Lorem ipsum dolor sit amet, consectetur adipiscing elit, sed do eiusmod tempor incididunt ut labore et dolore magna aliqu ad minim veniam, quisea.</p>
  <hr>
  <div class="person"><div class="avatar" role="img" aria-label="Client portrait"></div><div><b>JOHN SMITH,</b><small>USA</small></div></div>
</div>
<div class="abs dots"><i></i><i class="on"></i><i></i><i></i></div>

<!-- Contact -->
<div class="abs contact-photo" role="img" aria-label="Dark close-up of an off-road truck bumper with winch and tire"></div>
<svg class="abs" style="left:0;top:3370px" width="1200" height="240" viewBox="0 3370 1200 240">
  <polygon points="0,3392 418,3565 1200,3378 1200,3610 0,3610" fill="#0d0d0d"/>
  <polygon points="90,3385 418,3593 990,3395 418,3548" fill="#e3070e"/>
</svg>
<div class="abs" style="left:674px;top:2910px;font-size:15px;font-weight:700">CONTACT US</div>
<h2 class="abs display" style="left:674px;top:2930px;font-size:38px">Get In Touch</h2>
<div class="rule" style="left:641px;top:2980px"></div>

<div class="abs label" style="left:673px;top:3013px">First Name</div>
<div class="abs label" style="left:905px;top:3013px">Last Name</div>
<div class="abs field" style="left:673px;top:3041px;width:223px;height:44px"></div>
<div class="abs field" style="left:905px;top:3041px;width:222px;height:44px"></div>
<div class="abs label" style="left:673px;top:3098px">Phone</div>
<div class="abs label" style="left:905px;top:3098px">Email</div>
<div class="abs field" style="left:673px;top:3126px;width:223px;height:44px"></div>
<div class="abs field" style="left:905px;top:3126px;width:222px;height:44px"></div>
<div class="abs label" style="left:673px;top:3184px">Enquiry</div>
<div class="abs field" style="left:673px;top:3213px;width:454px;height:69px"></div>
<a class="abs btn" style="left:955px;top:3298px;width:172px;height:46px;font-size:14px">Send Message</a>

<!-- Footer -->
<div class="abs brand" style="left:111px;top:3768px;font-size:26px">Brisk Tow<span class="mark"></span></div>

<div class="abs f-head" style="left:428px">Company</div>
<ul class="abs f-links" style="left:428px"><li>Home</li><li>About Us</li><li>Blog</li><li>Contact Us</li></ul>
<div class="abs f-head" style="left:636px">Quick Links</div>
<ul class="abs f-links" style="left:636px"><li>Site Map</li><li>Privacy Policy</li><li>Terms Of Use</li><li>Disclaimer</li></ul>
<div class="abs f-head" style="left:870px">Contact Us</div>

<div class="abs ic" style="left:870px;top:3683px"><svg width="16" height="20" viewBox="0 0 16 20"><path fill="#fff" d="M8 0a7 7 0 0 0-7 7c0 5 7 13 7 13s7-8 7-13a7 7 0 0 0-7-7zm0 9.5A2.5 2.5 0 1 1 8 4.5a2.5 2.5 0 0 1 0 5z"/></svg></div>
<div class="abs c-text" style="left:930px;top:3682px">465, Lorum Ipsum Dolore Sed,<br>United States</div>
<div class="abs ic" style="left:870px;top:3735px"><svg width="18" height="18" viewBox="0 0 24 24"><path fill="#fff" d="M6.6 10.8a15.1 15.1 0 0 0 6.6 6.6l2.2-2.2c.3-.3.7-.4 1-.2 1.1.4 2.3.6 3.6.6.6 0 1 .4 1 1V20c0 .6-.4 1-1 1A17 17 0 0 1 3 4c0-.6.4-1 1-1h3.5c.6 0 1 .4 1 1 0 1.3.2 2.5.6 3.6.1.3 0 .7-.2 1z"/></svg></div>
<div class="abs c-text" style="left:930px;top:3733px"><b>PHONE:</b><br>+1 (888) 888 8888</div>
<div class="abs ic" style="left:870px;top:3788px"><svg width="18" height="14" viewBox="0 0 18 14"><rect width="18" height="14" rx="1" fill="#fff"/><path d="M1 1l8 6 8-6" stroke="#e3070e" stroke-width="2" fill="none"/></svg></div>
<div class="abs c-text" style="left:930px;top:3785px"><b>EMAIL:</b><br>info@brisktow.com</div>

<div class="abs foot-rule"></div>
<div class="abs copy">© 2024 &nbsp;BRISK TOW &nbsp;| &nbsp;All Rights Reserved</div>
<div class="abs f-social"><span class="on"><i></i></span><span><i></i></span><span><i></i></span><span><i></i></span></div>

</body>
</html>
```